Permanent Makeup (cosmetics salon) Brochure

We need a 2-4 sites brochure for our Permanent Makeup (cosmetics salon). Our company is based in Austria / Vienna. -> Our homepage is www.ek-morgenstaller.at
This brochure should show which treatments we provide ot our customers.

I've uploaded our old brochure, the content (text) would be nearly the same (look form "Must Haves", pics have to be new (look uploaded pics)
The old brochure is to dark. -> look for our homepage maybe you can make it like this

Target Market(s)

woman, age 25-70 years who wants to have permanent makeup on eyebrows, lips or eyeliner

Industry/Entity Type

Beauty Salon

Requirements
Must have
• pics which are uploaded.

*This text (somithing about our business)
"Für Frau Morgenstaller ist Permanent Makeup ein Kunsthandwerk. Das Team von EK-Morgenstaller ist spezialisiert auf natürliches Permanent Makeup damit der individuelle Typ jeder Kundin am schönsten zum Ausdruck kommt."

*We do this treatments: (english)
+ Augenbrauen Microblading (eyebrows)
+ Augenbrauen Permanent Makeup (eyebrows2)
+ Lidstrich Permanent Makeup (eyeliner)
+ Lip Blushing (lips)
+ Lippen Permanent Makeup (lips2)

* Our addresses (2 locations)
Wien
Lindengasse 7b/12, 1010 Wien
Tel: 01/5827710

Villach
Birkenrainweg 4, 9524 St. Ulrich
Tel: 0676/3159082

Mail: info@ek-morgenstaller.at
www.ek-morgenstaller.at

```html
<!DOCTYPE html>
<html lang="de">
<head>
<meta charset="utf-8">
<title>Elena Morgenstaller Kosmetikstudio – Broschüre</title>
<link rel="stylesheet" href="https://fonts.googleapis.com/css2?family=Josefin+Sans:wght@300;400&family=Great+Vibes&display=swap">
<style>
  :root {
    --board: #bcbdbf;
    --paper: #ffffff;
    --ink: #111111;
    --text: #1c1c1c;
    --gold: #d4b14a;
    --gold-light: #e8cf7a;
    --black: #000000;
  }
  * { margin: 0; padding: 0; box-sizing: border-box; }
  html, body { width: 783px; height: 1200px; overflow: hidden; }
  body { background: var(--board); position: relative; font-family: "Josefin Sans", sans-serif; font-weight: 300; color: var(--text); }
  h2 { font-weight: 300; }

  .page { position: absolute; width: 320px; height: 319px; background: var(--paper); box-shadow: 1px 2px 4px rgba(0,0,0,.18); overflow: hidden; }
  .page--cover { left: 55px; top: 112px; }
  .page--about { left: 55px; top: 451px; }
  .page--treatments { left: 397px; top: 451px; }
  .page--contact { left: 397px; top: 796px; }

  .photo { position: absolute; }

  .brand { position: absolute; text-align: center; color: var(--ink); }
  .brand__name { font-size: 12px; font-weight: 400; letter-spacing: .4px; white-space: nowrap; }
  .brand__sub { font-size: 4.4px; letter-spacing: 1.6px; margin-top: 5px; font-weight: 400; }

  .gold-tag { position: absolute; background: linear-gradient(90deg, var(--gold), var(--gold-light), var(--gold)); color: var(--ink); font-weight: 400; text-align: center; white-space: nowrap; }

  /* Cover */
  .cover__brand { left: 0; right: 0; top: 28px; }
  .cover__photo { left: 0; top: 72px; width: 320px; height: 122px; background: linear-gradient(90deg, #efe3cc 0%, #e6b79c 30%, #d89a82 60%, #b9684b 85%, #e2c59a 100%); }
  .cover__title { position: absolute; left: 0; right: 0; text-align: center; color: var(--ink); font-weight: 300; }
  .cover__title--main { top: 206px; font-size: 37px; line-height: 40px; }
  .cover__title--mid { top: 252px; font-size: 11.5px; line-height: 14px; }
  .cover__title--end { top: 264px; font-size: 31px; line-height: 34px; }
  .cover__tag { left: 110px; top: 297px; width: 99px; height: 9.5px; font-size: 6px; line-height: 10px; }

  /* About */
  .about__photo { left: 0; top: 0; width: 150px; height: 319px; background: linear-gradient(160deg, #b98c75 0%, #d6a88e 40%, #c08b73 65%, #5c6d79 100%); }
  .about__claim { position: absolute; left: 18px; top: 212px; width: 132px; height: 84px; background: var(--black); color: #fff; text-align: center; }
  .about__claim-lead { font-size: 8.5px; margin-top: 20px; }
  .about__claim-script { font-family: "Great Vibes", cursive; color: var(--gold); font-size: 11px; line-height: 10px; margin-top: 3px; }
  .about__claim-word { font-size: 15.5px; letter-spacing: .3px; margin-top: 2px; }
  .about__title { position: absolute; left: 170px; top: 30px; font-size: 30px; line-height: 34px; color: var(--ink); }
  .about__text { position: absolute; left: 170px; top: 70px; width: 138px; font-size: 6.8px; line-height: 9.4px; color: var(--text); }
  .about__eye { left: 169px; top: 144px; width: 137px; height: 113px; background: linear-gradient(135deg, #e9dcd5 0%, #c9a690 45%, #8c6a55 60%, #e8dcd8 100%); }
  .about__brand { left: 170px; width: 140px; top: 270px; }
  .about__brand .brand__name { font-size: 9px; }
  .about__brand .brand__sub { font-size: 3.6px; margin-top: 4px; }
  .about__tag { left: 184px; top: 303px; width: 112px; height: 7.5px; font-size: 4.5px; line-height: 8px; }

  /* Treatments */
  .treat__kicker { position: absolute; left: 31px; top: 38px; font-size: 11.5px; color: var(--ink); }
  .treat__title { position: absolute; left: 31px; top: 52px; font-size: 34px; line-height: 38px; color: var(--ink); }
  .treat__list { position: absolute; left: 30px; top: 117px; list-style: none; }
  .treat__list li { display: flex; align-items: center; gap: 4px; height: 14.4px; font-size: 7.2px; color: var(--text); }
  .treat__list li::before { content: ""; width: 5px; height: 5px; border-radius: 50%; border: 1px solid var(--gold); background: #f3e4b2; }
  .treat__lips-a { left: 8px; top: 205px; width: 156px; height: 105px; background: linear-gradient(180deg, #e9c6b2 0%, #d88a85 50%, #e8c3ad 100%); }
  .treat__lips-b { left: 170px; top: 205px; width: 139px; height: 105px; background: linear-gradient(180deg, #f1d0c4 0%, #d68b8a 55%, #f0cec2 100%); }

  /* Contact */
  .contact__intro { position: absolute; left: 0; right: 0; top: 33px; text-align: center; font-size: 7.2px; line-height: 9.4px; color: var(--text); }
  .contact__photo { left: 0; top: 72px; width: 320px; height: 123px; background: linear-gradient(90deg, #d3a88a 0%, #b9836a 40%, #8c5e4a 65%, #241a17 82%, #0a0a0a 100%); }
  .contact__brand { left: 38px; width: 120px; top: 229px; }
  .contact__brand .brand__name { font-size: 9.5px; }
  .contact__brand .brand__sub { font-size: 3.8px; margin-top: 4px; }
  .location { position: absolute; top: 272px; font-size: 6px; line-height: 8.4px; color: var(--text); white-space: nowrap; }
  .location--wien { left: 34px; }
  .location--villach { left: 124px; }
  .location__label { display: inline-block; padding: 1px 4px 0; margin-bottom: 1px; background: linear-gradient(90deg, var(--gold), var(--gold-light)); color: var(--ink); }
  .location__lines { padding-left: 4px; }
  .contact__web { position: absolute; left: 233px; top: 285px; font-size: 6px; line-height: 8.4px; color: var(--text); white-space: nowrap; }
</style>
</head>
<body>

  <section class="page page--cover">
    <div class="brand cover__brand">
      <div class="brand__name">Elena Morgenstaller</div>
      <div class="brand__sub">KOSMETIKSTUDIO</div>
    </div>
    <div class="photo cover__photo" role="img" aria-label="Close-up of a woman's eye and brow with blonde hair"></div>
    <div class="cover__title cover__title--main">Schönheit</div>
    <div class="cover__title cover__title--mid">kommt nicht nur von</div>
    <div class="cover__title cover__title--end">innen</div>
    <div class="gold-tag cover__tag">www.ek-morgenstaller.at</div>
  </section>

  <section class="page page--about">
    <div class="photo about__photo" role="img" aria-label="Portrait of a woman with natural makeup"></div>
    <div class="about__claim">
      <div class="about__claim-lead">Macht jeden Augenblick zu</div>
      <div class="about__claim-script">einer</div>
      <div class="about__claim-word">AUGENWEIDE</div>
    </div>
    <h2 class="about__title">About</h2>
    <p class="about__text">Für Frau Morgenstaller ist Permanent Makeup ein Kunsthandwerk. Das Team von EK-Morgenstaller ist spezialisiert auf natürliches Permanent Makeup damit der individuelle Typ jeder Kundin am schönsten zum Ausdruck kommt.</p>
    <div class="photo about__eye" role="img" aria-label="Close-up of an eye with a shaped brow"></div>
    <div class="brand about__brand">
      <div class="brand__name">Elena Morgenstaller</div>
      <div class="brand__sub">KOSMETIKSTUDIO</div>
    </div>
    <div class="gold-tag about__tag">info@ek-morgenstaller.at &nbsp;|&nbsp; www.ek-morgenstaller.at</div>
  </section>

  <section class="page page--treatments">
    <div class="treat__kicker">We do this</div>
    <h2 class="treat__title">Treatments</h2>
    <ul class="treat__list">
      <li>Augenbrauen Microblading (eyebrows)</li>
      <li>Augenbrauen Permanent Makeup (eyebrows2)</li>
      <li>Lidstrich Permanent Makeup (eyeliner)</li>
      <li>Lip Blushing (lips)</li>
      <li>Lippen Permanent Makeup (lips2)</li>
    </ul>
    <div class="photo treat__lips-a" role="img" aria-label="Close-up of lips with lip blushing"></div>
    <div class="photo treat__lips-b" role="img" aria-label="Close-up of lips with permanent lip makeup"></div>
  </section>

  <section class="page page--contact">
    <p class="contact__intro">Ihr Kosmetikstudio und Beauty Salon in 1010 Wien Professionelles Microblading<br>und Permanent Make Up für gehobene Ansprüche</p>
    <div class="photo contact__photo" role="img" aria-label="Close-up of an eye with long lashes and eyeliner"></div>
    <div class="brand contact__brand">
      <div class="brand__name">Elena Morgenstaller</div>
      <div class="brand__sub">KOSMETIKSTUDIO</div>
    </div>
    <div class="location location--wien">
      <span class="location__label">Wien</span>
      <div class="location__lines">Lindengasse 7b/12, 1010 Wien<br>Tel: 01/5827710</div>
    </div>
    <div class="location location--villach">
      <span class="location__label">Villach</span>
      <div class="location__lines">Birkenrainweg 4, 9524 St. Ulrich<br>Tel: 0676/3159082</div>
    </div>
    <div class="contact__web">info@ek-morgenstaller.at<br>www.ek-morgenstaller.at</div>
  </section>

</body>
</html>
```